BildeVOLD buisnesscard

Hey :) I need a modern buisnesscard for my company BildeVOLD
It most have:
Dagligleder og Fotograf: Henrik Audun Strandvik

Mob: +4791264085
Epost: post@bildevold.example
Adresse: Kvernbakken9, 6040 Langevåg

Facbook and instagram logo with text BildeVOLD

BildeVOLD logo

It Company

```html
<!DOCTYPE html>
<html lang="no">
<head>
<meta charset="utf-8">
<title>BildeVOLD – visittkort</title>
<link rel="stylesheet" href="https://fonts.googleapis.com/css2?family=Lato:wght@400;700;900&display=swap">
<style>
  :root {
    --ink: #000000;
    --paper: #ffffff;
    --silver: #b4b4b6;
    --muted: #c2c2c4;
    --stage: #e6e6e8;
  }
  * { box-sizing: border-box; margin: 0; padding: 0; }
  html, body {
    width: 1200px; height: 900px; overflow: hidden;
    background: var(--stage);
    font-family: "Lato", sans-serif;
  }
  .canvas {
    width: 1200px; height: 900px;
    display: flex; flex-direction: column; align-items: center; justify-content: center;
    gap: 40px;
  }
  .card {
    position: relative;
    width: 700px; height: 400px;
    overflow: hidden;
    box-shadow: 0 6px 18px rgba(0,0,0,.18);
  }
  .card--back { background: var(--ink); }
  .card--front { background: var(--paper); }
  .card__waves { position: absolute; inset: 0; width: 100%; height: 100%; }

  .wordmark {
    position: absolute;
    display: flex; align-items: center; gap: 14px;
    color: var(--silver);
    font-weight: 900;
    letter-spacing: .5px;
    white-space: nowrap;
  }
  .wordmark__square { width: 0.9em; height: 0.9em; background: var(--silver); }
  .card--back .wordmark {
    left: 50%; top: 50%; transform: translate(-50%, -50%);
    font-size: 72px;
  }
  .card--front .wordmark {
    left: 36px; top: 62px;
    font-size: 50px;
  }

  .person { position: absolute; left: 380px; top: 118px; }
  .person__name { font-size: 27px; font-weight: 400; color: var(--ink); white-space: nowrap; }
  .person__title { font-size: 16px; color: var(--muted); margin-top: 2px; }

  .contact {
    position: absolute; left: 400px; top: 262px;
    color: var(--paper); font-size: 16px; line-height: 20px;
  }
  .contact__address { margin-left: 32px; margin-bottom: 4px; }
  .contact__list { list-style: none; }
  .contact__item { display: flex; align-items: center; gap: 14px; white-space: nowrap; }
  .contact__icon { width: 18px; height: 18px; flex: none; }
</style>
</head>
<body>
<main class="canvas">

  <section class="card card--back" aria-label="Baksiden av visittkortet">
    <div class="wordmark"><span class="wordmark__square"></span>BildeVOLD</div>
  </section>

  <section class="card card--front" aria-label="Forsiden av visittkortet">
    <svg class="card__waves" viewBox="0 0 700 400" preserveAspectRatio="none" aria-hidden="true">
      <g transform="translate(0,-22)">
        <path d="M0 180 C 40 215, 150 225, 330 232 C 500 240, 630 250, 700 290 L700 430 L0 430 Z" fill="var(--silver)"/>
        <path d="M0 200 C 60 232, 200 240, 360 250 C 520 260, 640 270, 700 305 L700 430 L0 430 Z" fill="var(--paper)"/>
        <path d="M0 208 C 70 245, 230 252, 370 262 C 540 275, 650 280, 700 310 L700 430 L0 430 Z" fill="var(--ink)"/>
      </g>
    </svg>

    <div class="wordmark"><span class="wordmark__square"></span>BildeVOLD</div>

    <div class="person">
      <p class="person__name">Henrik Audun Strandvik</p>
      <p class="person__title">Dagligleder og Fotograf</p>
    </div>

    <div class="contact">
      <p class="contact__address">Kvernbakken 9<br>6040 Solbakkvik</p>
      <ul class="contact__list">
        <li class="contact__item">
          <svg class="contact__icon" viewBox="0 0 18 18" aria-hidden="true"><rect x="5" y="1" width="8" height="16" rx="1.5" fill="none" stroke="var(--paper)" stroke-width="1.4"/><rect x="6.5" y="3" width="5" height="8" fill="var(--paper)"/></svg>
          <span>+4791264085</span>
        </li>
        <li class="contact__item">
          <svg class="contact__icon" viewBox="0 0 18 18" aria-hidden="true"><rect x="1" y="4" width="16" height="11" fill="var(--paper)"/><path d="M1 4 L9 11 L17 4" fill="none" stroke="var(--ink)" stroke-width="1.2"/></svg>
          <span>post@bildevold.example</span>
        </li>
        <li class="contact__item">
          <svg class="contact__icon" viewBox="0 0 18 18" aria-hidden="true"><rect x="2" y="2" width="14" height="14" fill="var(--muted)"/></svg>
          <span>BildeVOLD</span>
        </li>
        <li class="contact__item">
          <svg class="contact__icon" viewBox="0 0 18 18" aria-hidden="true"><circle cx="9" cy="9" r="7" fill="var(--paper)"/></svg>
          <span>BildeVOLD</span>
        </li>
      </ul>
    </div>
  </section>

</main>
</body>
</html>
```